First Annual Whitaker Family Reunion

Family reunion invitation, please see the attached letter for the language. Also provided a picture of my grandparents, if you could include it on a letter or brochure. I'm flexible.
Updates

I just uploaded a Word document with the time, address, and list of activities. Please click on the hyperlink, it takes you directly to our Family Reunion webpage and click on Agenda for all details.

Target Market(s)

Family and Friends invitation

Requirements
Must have
• Date, time, picture, family logo, and website for payment

```html
<!DOCTYPE html>
<html lang="en">
<head>
<meta charset="utf-8">
<title>Whitaker Family Reunion 2023</title>
<link href="https://fonts.googleapis.com/css2?family=Sofia&family=Caveat:wght@400&family=Cinzel:wght@700&family=Fredoka:wght@700&family=Open+Sans:wght@400;600;700&display=swap" rel="stylesheet">
<style>
  :root {
    --page: #ffffff;
    --ink-bg: #24313a;
    --ink-bg-soft: #2c3b44;
    --white: #ffffff;
    --cream: #f3ece0;
    --gold: #e1b24a;
    --gold-light: #f2d27c;
    --gold-dark: #b98a2c;
    --banner-text: #2a2a22;
    --peach: #f6a48c;
    --orange: #f49a56;
    --teal: #3aa58a;
    --green: #5a9a3a;
    --blush: #f3c8b8;
    --rose: #d9697a;
  }
  * { margin: 0; padding: 0; box-sizing: border-box; }
  html, body { width: 1200px; height: 1200px; overflow: hidden; background: var(--page); }
  .poster {
    position: absolute; left: 150px; top: 0; width: 900px; height: 1200px;
    background: radial-gradient(ellipse at 50% 25%, var(--ink-bg-soft) 0%, var(--ink-bg) 55%);
    overflow: hidden; color: var(--white);
  }
  .floral { position: absolute; border-radius: 50%; filter: blur(2px); }
  .floral--top-left { left: 0; top: -20px; width: 170px; height: 140px; background: radial-gradient(circle, var(--blush) 0%, rgba(243,200,184,.5) 45%, rgba(90,154,58,.35) 70%, transparent 72%); }
  .floral--top-center { left: 297px; top: -40px; width: 120px; height: 120px; background: radial-gradient(circle, var(--peach) 0%, rgba(246,164,140,.8) 55%, transparent 70%); }
  .floral--top-right { left: 740px; top: -40px; width: 220px; height: 300px; background: radial-gradient(ellipse at 70% 25%, var(--orange) 0%, rgba(244,154,86,.8) 35%, rgba(58,165,138,.55) 60%, transparent 72%); }
  .floral--right-berries { left: 820px; top: 280px; width: 110px; height: 130px; background: radial-gradient(circle, rgba(243,200,184,.55) 0%, rgba(243,200,184,.25) 50%, transparent 70%); }
  .floral--right-middle { left: 820px; top: 390px; width: 140px; height: 180px; background: radial-gradient(circle at 70% 50%, var(--peach) 0%, rgba(246,164,140,.8) 45%, rgba(90,154,58,.3) 62%, transparent 72%); }
  .floral--left-edge { left: -50px; top: 190px; width: 90px; height: 340px; background: radial-gradient(ellipse, rgba(90,154,58,.55) 0%, transparent 70%); }
  .floral--left-bottom { left: -60px; top: 560px; width: 260px; height: 660px; background: radial-gradient(ellipse at 40% 50%, rgba(244,120,80,.9) 0%, rgba(246,164,140,.6) 30%, rgba(58,165,138,.6) 55%, transparent 72%); }
  .floral--bottom-center { left: 140px; top: 1090px; width: 180px; height: 160px; background: radial-gradient(circle, var(--peach) 0%, rgba(126,196,176,.6) 45%, transparent 70%); }
  .floral--bottom-right { left: 740px; top: 870px; width: 220px; height: 380px; background: radial-gradient(ellipse at 65% 60%, rgba(217,105,122,.75) 0%, rgba(244,154,86,.7) 40%, rgba(58,165,138,.4) 58%, transparent 72%); }

  .family-mark {
    position: absolute; left: 0; width: 100%; top: 118px;
    display: flex; justify-content: center; align-items: center; gap: 8px;
    font-family: "Open Sans", sans-serif; font-weight: 600; font-size: 13px;
    letter-spacing: 1.5px; color: var(--white);
  }
  .family-mark__dot { width: 10px; height: 10px; border-radius: 50%; background: var(--white); }

  .photo-collage { position: absolute; left: 220px; top: 188px; width: 420px; height: 250px; }

  .title {
    position: absolute; left: 0; width: 100%; top: 455px; text-align: center;
    font-family: "Sofia", cursive; font-size: 118px; line-height: 1; color: var(--white);
  }
  .title__year {
    position: absolute; left: 647px; top: 578px;
    font-family: "Fredoka", sans-serif; font-weight: 700; font-size: 34px; letter-spacing: 1px;
    color: var(--gold);
  }

  .letter {
    position: absolute; left: 142px; top: 646px; width: 682px;
    font-family: "Caveat", cursive; font-size: 19.5px; line-height: 25px; color: var(--white);
  }
  .letter__greeting { font-size: 21px; margin-bottom: 1px; }
  .letter__body { text-align: justify; text-align-last: center; }
  .letter__opening { display: block; text-align: center; }

  .date-banner { position: absolute; left: 278px; top: 874px; width: 350px; height: 58px; }
  .date-banner__text {
    position: absolute; left: 278px; top: 874px; width: 350px; height: 58px;
    display: flex; align-items: center; justify-content: center;
    font-family: "Cinzel", serif; font-weight: 700; font-size: 15.5px; letter-spacing: .5px;
    color: var(--banner-text);
  }

  .details {
    position: absolute; left: 0; width: 100%; text-align: center;
    font-family: "Open Sans", sans-serif; color: var(--white); letter-spacing: 1.2px;
  }
  .details--activities { top: 944px; font-size: 11.5px; line-height: 13.5px; }
  .details--rsvp { top: 997px; font-size: 10px; line-height: 12px; }
  .details__link { color: var(--gold); font-weight: 700; font-size: 11px; }
  .signature {
    position: absolute; left: 0; width: 100%; top: 1124px; text-align: center;
    font-family: "Open Sans", sans-serif; font-size: 12px; letter-spacing: 1.2px; color: var(--white);
  }
</style>
</head>
<body>
<main class="poster">
  <div class="floral floral--top-left" role="img" aria-label="Illustrated pale pink blossoms with green sprigs"></div>
  <div class="floral floral--top-center" role="img" aria-label="Illustrated peach flower with berry stems"></div>
  <div class="floral floral--top-right" role="img" aria-label="Illustrated orange daisy and teal leaf"></div>
  <div class="floral floral--right-berries" role="img" aria-label="Illustrated blush berry sprig"></div>
  <div class="floral floral--right-middle" role="img" aria-label="Illustrated peach flower with green leaves"></div>
  <div class="floral floral--left-edge" role="img" aria-label="Illustrated green leaf stems"></div>
  <div class="floral floral--left-bottom" role="img" aria-label="Illustrated coral tulip, peach blossoms, teal leaf and orange daisy"></div>
  <div class="floral floral--bottom-center" role="img" aria-label="Illustrated peach flower and mint leaves"></div>
  <div class="floral floral--bottom-right" role="img" aria-label="Illustrated pink roses, butterfly and orange daisy"></div>

  <div class="family-mark"><span class="family-mark__dot"></span>Whitaker Family Reunion</div>

  <svg class="photo-collage" viewBox="0 0 420 250" role="img" aria-label="Collage of nine circular family photographs, including grandparents, a graduate and group gatherings">
    <ellipse cx="210" cy="125" rx="215" ry="130" fill="#3a4a52" opacity=".55"/>
    <g stroke="#ffffff" stroke-width="2.5">
      <circle cx="60" cy="68" r="53" fill="#6a7f96"/>
      <circle cx="155" cy="55" r="53" fill="#6b7a4e"/>
      <circle cx="245" cy="80" r="52" fill="#8b6a4a"/>
      <circle cx="340" cy="58" r="58" fill="#3a3430"/>
      <circle cx="56" cy="174" r="55" fill="#c49a3a"/>
      <circle cx="152" cy="160" r="58" fill="#5a3a34"/>
      <circle cx="247" cy="180" r="55" fill="#6e6e72"/>
      <circle cx="338" cy="164" r="55" fill="#5e4c42"/>
    </g>
  </svg>

  <h1 class="title">Family Reunion</h1>
  <div class="title__year">2023</div>

  <section class="letter">
    <p class="letter__greeting">Dear Family,</p>
    <p class="letter__body"><span class="letter__opening">I hope this letter finds all of you in good health and high spirits.</span>Our family, which is spread across different parts of the country, rarely gets an opportunity to gather together under one roof, but I am excited to inform you that we have finally planned a family reunion. It has been long overdue, and we are looking forward to catching up with everyone, reminiscing old memories, and creating some new ones over the course of this event. I cannot emphasize enough on how important this reunion will be for our family. We have come to learn over the years that nothing can ever replace the love and connections that we share between us.</p>
  </section>

  <svg class="date-banner" viewBox="0 0 350 58" aria-hidden="true">
    <defs>
      <linearGradient id="gold-fill" x1="0" y1="0" x2="1" y2="0">
        <stop offset="0" stop-color="#d9a73e"/>
        <stop offset=".5" stop-color="#f2d27c"/>
        <stop offset="1" stop-color="#c8922e"/>
      </linearGradient>
    </defs>
    <path d="M14 3 H336 L349 29 L336 55 H14 L1 29 Z" fill="none" stroke="#e1b24a" stroke-width="1.5"/>
    <path d="M19 7 H331 L342 29 L331 51 H19 L8 29 Z" fill="url(#gold-fill)"/>
  </svg>
  <div class="date-banner__text">September 1 2023 to September 3 2023</div>

  <p class="details details--activities">Fun-filled weekend filled with activities for all ages,<br>which will include games, music, storytelling, and much more.</p>
  <p class="details details--rsvp">Please RSVP and pay your deposit as soon as possible at <span class="details__link">https://whitakerreunion.net</span><br>so that we can make arrangements accordingly.<br>Also, please notify any family members who may have been left out or forgotten.</p>

  <p class="signature">The Whitaker’s Family Committee</p>
</main>
</body>
</html>
```